Redesign This Psychology Website

We would like a slight redesign of this successful psychology (relationship counselling) website:

www.TheKelvaleClinic.com.au

We are updating the website, and we'd like a slight refresh of the design and style.

Please keep to very similar colours, and use the same logo. We're looking for around 10 page templates, however the main one is the home page.

Keep in mind, this website already converts quite well, so we want a new, fresh design in keeping with this one. Please don't bother designing something too extremely different.

thanks :)

Target Market(s)

couples who are looking for relationship counselling. Men and women, 25 - 70, across Australia

Industry/Entity Type

Psychology

Number of Pages Required

5+ page

Font styles to use
Sans Serif

Colors
87cfc6
b7a5cd
ec1f27
ffffff
cee9f5

Requirements
Must have
• a similar look to the current design, just looking for a slight refresh.
• Search bar
• Areas for lots of photos
• same logo
• lots of content areas
Nice to have
• great content areas, where we can display a lot of content and our areas.
Should not have
• no colors like orange, etc.
• should not have a totally different feel.

```html
<!DOCTYPE html>
<html lang="en">
<head>
<meta charset="utf-8">
<title>The Kelvale Clinic – Relationship Counselling</title>
<link href="https://fonts.googleapis.com/css2?family=Open+Sans:wght@400;600;700&family=Roboto:wght@300;400;500;700&display=swap" rel="stylesheet">
<style>
:root{
  --teal:#87cfc6;
  --teal-dark:#5fbfb2;
  --red:#ec1f27;
  --lilac:#b7a5cd;
  --sky:#cee9f5;
  --ink:#555;
  --muted:#8a8a8a;
  --line:#e3e3e3;
  --pale:#f3f4f5;
  --white:#fff;
}
*{box-sizing:border-box;margin:0;padding:0}
html,body{width:1200px;height:3696px;overflow:hidden}
body{font-family:"Open Sans",Arial,sans-serif;color:var(--ink);background:var(--white);font-size:12px;line-height:1.9}
.wrap{width:1028px;margin:0 auto;position:relative}
.photo{background:linear-gradient(135deg,#d9c8bb,#a98f80 60%,#7d6a62)}
.photo.cool{background:linear-gradient(135deg,#cfd6dc,#8f9aa3 60%,#5f6870)}
.photo.warm{background:linear-gradient(135deg,#e9d7c7,#c3a18a 60%,#8d7162)}
.photo.soft{background:linear-gradient(135deg,#eee6e0,#cdbfb6 60%,#a8978c)}
/* header */
.topbar{height:98px}
.topbar .wrap{height:98px;display:flex;align-items:center;justify-content:space-between}
.brand{display:flex;align-items:center;gap:10px;font-family:Roboto,sans-serif;font-weight:500;font-size:22px;color:var(--teal-dark);white-space:nowrap;line-height:1.2}
.brand .dot{width:26px;height:26px;border-radius:50%;background:var(--teal-dark);flex:none}
.search{display:flex;width:438px;height:36px;margin-left:90px}
.search .field{flex:1;background:#f2f2f2;border:1px solid var(--line);border-right:0;display:flex;align-items:center;padding-left:14px;gap:8px;color:#aaa;font-size:11px}
.search .btn{width:82px;background:var(--teal);color:#fff;font-weight:700;font-size:12px;display:flex;align-items:center;justify-content:center}
.call{display:flex;align-items:center;gap:12px;font-family:Roboto,sans-serif;font-size:17px;color:#444;white-space:nowrap}
.call .ic{width:46px;height:46px;border-radius:50%;background:var(--red);display:flex;align-items:center;justify-content:center}
.nav{height:55px;background:var(--teal)}
.nav .wrap{height:55px;display:flex;align-items:center;justify-content:space-between}
.nav ul{list-style:none;display:flex}
.nav li{color:#fff;font-size:12px;font-weight:600;padding:0 24px;border-right:1px solid rgba(255,255,255,.4);line-height:16px}
.nav li:last-child{border-right:0}
.social{display:flex;gap:8px}
.social span{width:32px;height:32px;border:1.5px solid #fff;border-radius:50%;display:block}
/* hero */
.hero{height:487px;position:relative;background:linear-gradient(90deg,#f4f6f8 0%,#eef2f5 40%,#dfe8ee 60%)}
.hero-photo{position:absolute;right:0;top:0;width:620px;height:487px;background:linear-gradient(110deg,#eef2f5 0%,#b9d4e3 20%,#3c98b8 60%,#2d7f9c)}
.hero-copy{position:absolute;left:86px;top:128px;width:440px}
.hero-copy .brand{font-size:34px;margin-bottom:44px;gap:12px}
.hero-copy .brand .dot{width:40px;height:40px}
.hero-copy p{font-size:12px;line-height:2.2;color:#555}
.btn-red{display:inline-block;margin-top:28px;background:var(--red);color:#fff;font-weight:600;font-size:13px;width:143px;height:44px;line-height:44px;text-align:center;border-radius:3px;white-space:nowrap}
.dots{position:absolute;left:86px;bottom:12px;display:flex;gap:6px}
.dots i{width:12px;height:12px;border:1.5px solid #999;border-radius:50%;display:block}
.dots i.on{border-color:var(--red)}
/* intro */
.intro{height:525px;padding-top:47px}
.intro .row{display:flex;gap:42px}
.video{width:537px;height:326px;position:relative;flex:none}
.video .play{position:absolute;left:228px;top:118px;width:80px;height:80px;border:3px solid #fff;border-radius:50%}
.video .play:after{content:"";position:absolute;left:30px;top:21px;border-left:26px solid #fff;border-top:16px solid transparent;border-bottom:16px solid transparent}
.intro h3{font-family:Roboto,sans-serif;font-weight:400;font-size:15px;color:#666;margin-top:2px}
.intro h2{font-family:Roboto,sans-serif;font-weight:700;font-size:26px;color:var(--teal);margin:4px 0 14px}
.intro .txt p{font-size:11px;line-height:2.3;color:var(--muted);margin-bottom:18px}
.intro .full{font-size:11px;line-height:2.3;color:var(--muted);margin-top:26px}
/* services */
.services{height:412px;background:var(--pale);padding-top:35px}
.cards{display:flex;gap:15px}
.card{width:246px}
.card .photo{height:160px}
.card h4{font-family:Roboto,sans-serif;font-weight:500;font-size:12px;color:var(--teal);margin:20px 0 8px}
.card p{font-size:11px;line-height:2;color:var(--muted);height:66px}
.card a{display:block;margin-top:18px;font-size:10px;color:var(--teal-dark);text-decoration:underline}
/* teal band */
.band{height:370px;background:var(--teal);color:#fff}
.band .wrap{display:flex;height:370px}
.band .left{width:630px;padding-top:44px;border-right:1px solid rgba(255,255,255,.45);margin-bottom:30px}
.band .right{padding:44px 0 0 24px;flex:1}
.band h5{font-family:Roboto,sans-serif;font-weight:500;font-size:14px;margin-left:42px}
.band .right h5{margin-left:0}
.band .sub{font-size:11px;margin:10px 0 34px 86px}
.locs{display:grid;grid-template-columns:230px 180px 180px;margin-left:42px;font-size:11px;row-gap:6px}
.locs span:not(:empty):before{content:"";display:inline-block;width:5px;height:5px;background:#fff;border-radius:50%;margin-right:26px;vertical-align:middle}
.approach{display:flex;gap:22px;margin-top:40px}
.approach .photo{width:136px;height:136px;border-radius:50%;border:4px solid #fff;flex:none;background:linear-gradient(135deg,#f0d9a8,#c9a46e)}
.approach p{font-size:10.5px;line-height:2.2}
.approach .sig{margin-top:16px;font-size:10px;line-height:1.8}
/* blog */
.blog{height:912px;padding-top:47px;text-align:center}
.sec-title{font-family:Roboto,sans-serif;font-weight:400;font-size:24px;color:#666;letter-spacing:.5px}
.sec-sub{font-size:10px;color:var(--muted);margin-top:4px}
.posts{display:grid;grid-template-columns:repeat(3,330px);column-gap:19px;row-gap:56px;margin-top:28px;text-align:left}
.post .photo{height:198px}
.post h4{font-family:Roboto,sans-serif;font-weight:500;font-size:12px;color:var(--teal);margin:26px 0 12px}
.post p{font-size:11px;line-height:2.2;color:#666}
.meta{display:flex;gap:18px;margin-top:14px;font-size:11px;color:var(--teal-dark)}
.meta span{display:flex;align-items:center;gap:6px}
/* partners */
.partners{height:197px;background:var(--pale)}
.partners .wrap{height:197px;display:flex;align-items:center;justify-content:center;gap:34px}
.badge{width:177px;height:99px;background:#fff;border:1px solid var(--line);display:flex;align-items:center;justify-content:center}
.badge i{display:block;width:110px;height:34px;border-radius:4px}
.chev{position:absolute;top:80px;width:16px;height:36px}
/* gallery */
.gallery{height:332px;padding-top:36px;text-align:center}
.strip{display:flex;gap:4px;margin-top:30px}
.strip .photo{flex:1;height:167px}
/* footer */
.footer{height:264px;background:var(--pale)}
.footer .wrap{display:flex;padding-top:48px}
.footer .logo-col{width:290px;padding-top:50px}
.footer h6{font-family:Roboto,sans-serif;font-weight:500;font-size:14px;color:#555;margin-bottom:14px}
.footer .col{font-size:10.5px;color:#666;line-height:1.9}
.contact li{list-style:none;display:flex;gap:12px;align-items:flex-start;margin-bottom:8px}
.contact li i{width:11px;height:11px;background:#888;display:block;margin-top:4px;flex:none}
.email{width:210px;height:32px;border:1px solid #ccc;background:#fff;font-size:10px;color:#999;padding:6px 10px;margin:14px 0 10px}
.subscribe{display:inline-block;background:var(--red);color:#fff;font-size:10px;font-weight:600;padding:3px 10px}
.fsocial{display:flex;gap:8px;margin-top:18px}
.fsocial span{width:30px;height:30px;border:1px solid #aaa;border-radius:50%;display:block}
.copyright{height:69px;background:var(--teal);color:#fff;font-size:10px;display:flex;align-items:center;justify-content:center}
</style>
</head>
<body>

<header class="topbar">
  <div class="wrap">
    <div class="brand"><span class="dot"></span>The Kelvale Clinic</div>
    <div class="search">
      <div class="field">
        <svg width="12" height="12" viewBox="0 0 12 12"><circle cx="5" cy="5" r="3.8" fill="none" stroke="#999" stroke-width="1.4"/><line x1="8" y1="8" x2="11" y2="11" stroke="#999" stroke-width="1.4"/></svg>
        Enter Your Keyword ...
      </div>
      <div class="btn">SEARCH</div>
    </div>
    <div class="call">
      <span class="ic"><svg width="20" height="20" viewBox="0 0 24 24"><path d="M6.6 10.8a15 15 0 0 0 6.6 6.6l2.2-2.2c.3-.3.7-.4 1-.2 1.1.4 2.3.6 3.6.6.6 0 1 .4 1 1V20c0 .6-.4 1-1 1A17 17 0 0 1 3 4c0-.6.4-1 1-1h3.5c.6 0 1 .4 1 1 0 1.3.2 2.5.6 3.6.1.3 0 .7-.2 1z" fill="#fff"/></svg></span>
      CALL US : 1300 555 014
    </div>
  </div>
</header>

<nav class="nav">
  <div class="wrap">
    <ul><li>HOME</li><li>ABOUT</li><li>RESOURCES</li><li>BLOG</li><li>SHOP</li><li>CART</li><li>CONTACT US</li></ul>
    <div class="social"><span></span><span></span><span></span><span></span><span></span></div>
  </div>
</nav>

<section class="hero">
  <div class="hero-photo" role="img" aria-label="Smiling couple embracing outdoors"></div>
  <div class="hero-copy">
    <div class="brand"><span class="dot"></span>The Kelvale Clinic</div>
    <p>At the Kelvale Clinic, we are a group of PSYCHOLOGISTS, Australia wide who are passionate about relationships and helping you with yours. Our vision is to provide regarded and comprehensive marriage counselling ...</p>
    <span class="btn-red">READ MORE</span>
  </div>
  <div class="dots"><i></i><i class="on"></i><i></i></div>
</section>

<section class="intro">
  <div class="wrap">
    <div class="row">
      <div class="video photo warm" role="img" aria-label="Video still of the clinic director with a couple">
        <span class="play"></span>
      </div>
      <div class="txt" style="flex:1">
        <h3>WE SPECIALISE IN RELATIONSHIP</h3>
        <h2>MARRIAGE COUNSELLING</h2>
        <p>At the Kelvale Clinic, we are a group of PSYCHOLOGISTS, Australia wide who are passionate about relationships and helping you with yours. Our vision is to provide the most highly regarded and comprehensive marriage counselling and sex therapy in Australia, at reasonable and affordable rates about relationships and helping you with yours. Our vision is to provide the most highly regarded about relationships &amp; the most highly regarded marriage.</p>
        <p>When we are experiencing relationship and marriage problems, there can be a lot of pain and confusion, and it can often be difficult to cope with the other as all of our lives when we are struggling with problems with our partner.</p>
      </div>
    </div>
    <p class="full">At the Kelvale Clinic, we are a group of PSYCHOLOGISTS, Australia wide who are passionate about relationships and helping you with yours. Our vision is to provide the most highly regarded and comprehensive marriage counselling and sex therapy in Australia, at reasonable and affordable rates about relationships and helping you with yours. Our vision is to provide the most highly regarded Australia wide who are passionate about relationships and helping you with yours. Our vision is regarded.</p>
  </div>
</section>

<section class="services">
  <div class="wrap cards">
    <div class="card"><div class="photo soft" role="img" aria-label="Happy couple smiling together"></div><h4>RELATIONSHIP COUNSELLING</h4><p>Communication, Recovering from an affair, Loss of intimacy &amp; love, Power battles, Feeling like friends, not lovers</p><a>READ MORE</a></div>
    <div class="card"><div class="photo warm" role="img" aria-label="Couple laughing in bed"></div><h4>SEX THERAPY COUNSELLING</h4><p>Low libido, Erectile difficulties, Premature ejaculation, Differing libidos, Porn addiction, Keeping sex exciting</p><a>READ MORE</a></div>
    <div class="card"><div class="photo cool" role="img" aria-label="Upset woman sitting alone"></div><h4>ANGER MANAGEMENT COUNSELLING</h4><p>Managing angry outbursts, expressing your anger in healthy ways. Managing angry outbursts, expressing your anger</p><a>READ MORE</a></div>
    <div class="card"><div class="photo soft" role="img" aria-label="Woman holding a flower"></div><h4>NARCISSISM COUNSELLING</h4><p>Managing narcissistic, superior, entitled, arrogant and lack of empathy tendencies in you or your partner</p><a>READ MORE</a></div>
  </div>
</section>

<section class="band">
  <div class="wrap">
    <div class="left">
      <h5>OUR RELATIONSHIP COUNSELLING LOCATIONS ACROSS AUSTRALIA</h5>
      <p class="sub">We currently have relationship counselling and marriage counselling services in</p>
      <div class="locs">
        <span>Sydney – 10 centres</span><span>Wollongong – 1 centre</span><span>Cairns – 1 centre</span>
        <span>Canberra – 2 centres</span><span>Central Coast – 2 centres</span><span>Townsville – 1 centre</span>
        <span>Melbourne – 11 centres</span><span>Adelaide – 4 centres</span><span>Wodonga – 1 centre</span>
        <span>Perth – 12 centres</span><span>Gold Coast – 5 centres</span><span></span>
        <span>Brisbane – 14 centres</span><span>Sunshine Coast – 2 centres</span><span></span>
      </div>
    </div>
    <div class="right">
      <h5>OUR RELATIONSHIP COUNSELLING APPROACH</h5>
      <div class="approach">
        <div class="photo" role="img" aria-label="Portrait of the clinic director"></div>
        <div>
          <p>So learning how to communicate your honest thoughts and feelings in a way that your partner does truly listen is a crucial skill for you to feel that you are in a fulfilling relationship. We can show you some simple but effective principles on how to do this with each other.</p>
          <p class="sig">DANA MERRITT<br>Director – Psychologist</p>
        </div>
      </div>
    </div>
  </div>
</section>

<section class="blog">
  <div class="wrap">
    <h2 class="sec-title">LATEST BLOG</h2>
    <p class="sec-sub">Certain clinics also provide after hours and Saturday sessions for your convenience</p>
    <div class="posts">
      <article class="post"><div class="photo cool" role="img" aria-label="Couple sitting apart after an argument"></div><h4>WHY AM I WITH A NARCISSIST?</h4><p>Finding yourself in a "whirlwind romance", he/she will appear to be all you have ever wanted in a partner</p><div class="meta"><span>▢ February 24, 2017</span><span>◻ 00 Comments</span></div></article>
      <article class="post"><div class="photo warm" role="img" aria-label="Woman upset during a conversation"></div><h4>HOW DO I KNOW IF I'M WITH A NARCISSIST?</h4><p>However, our relationship with our partner is arguably the most important thing in our lives and actually.</p><div class="meta"><span>▢ February 24, 2017</span><span>◻ 00 Comments</span></div></article>
      <article class="post"><div class="photo soft" role="img" aria-label="Couple in counselling session"></div><h4>RELATIONSHIP COUNSELLING</h4><p>However, our relationship with our partner is arguably the most important thing in our lives and actually.</p><div class="meta"><span>▢ February 2, 2017</span><span>◻ 00 Comments</span></div></article>
      <article class="post"><div class="photo cool" role="img" aria-label="Two men sitting in conversation"></div><h4>SAME SEX RELATIONSHIPS &amp; COUNSELLING</h4><p>Finding yourself in a "whirlwind romance", he/she will appear to be all you have ever wanted in a partner</p><div class="meta"><span>▢ February 24, 2017</span><span>◻ 00 Comments</span></div></article>
      <article class="post"><div class="photo warm" role="img" aria-label="Couple arguing at home"></div><h4>HOW TO DEAL WITH AN AFFAIR?</h4><p>However, our relationship with our partner is arguably the most important thing in our lives and actually.</p><div class="meta"><span>▢ February 24, 2017</span><span>◻ 00 Comments</span></div></article>
      <article class="post"><div class="photo cool" role="img" aria-label="Distressed woman holding her head"></div><h4>ARE YOU LIVING WITH A NARCISSIST</h4><p>However, our relationship with our partner is arguably the most important thing in our lives and actually.</p><div class="meta"><span>▢ February 2, 2017</span><span>◻ 00 Comments</span></div></article>
    </div>
  </div>
</section>

<section class="partners">
  <div class="wrap">
    <svg class="chev" style="left:-40px" viewBox="0 0 16 36"><polyline points="14,2 2,18 14,34" fill="none" stroke="#ccc" stroke-width="2"/></svg>
    <div class="badge"><i style="background:#f2c230"></i></div>
    <div class="badge"><i style="background:#e8343b"></i></div>
    <div class="badge"><i style="background:#3b9cd2"></i></div>
    <div class="badge"><i style="background:#4cc0d8"></i></div>
    <div class="badge"><i style="background:#45b548"></i></div>
    <svg class="chev" style="right:-40px" viewBox="0 0 16 36"><polyline points="2,2 14,18 2,34" fill="none" stroke="#ccc" stroke-width="2"/></svg>
  </div>
</section>

<section class="gallery">
  <div class="wrap">
    <h2 class="sec-title">PHOTO GALLERY</h2>
    <p class="sec-sub">Certain clinics also provide after hours and Saturday sessions for your convenience</p>
    <div class="strip">
      <div class="photo cool" role="img" aria-label="Couple in a quiet moment"></div>
      <div class="photo warm" role="img" aria-label="Couple laughing together"></div>
      <div class="photo soft" role="img" aria-label="Couple at a counselling session"></div>
      <div class="photo warm" role="img" aria-label="Woman in a counselling room"></div>
      <div class="photo soft" role="img" aria-label="Couple talking on a sofa"></div>
      <div class="photo cool" role="img" aria-label="Clinic consulting room"></div>
    </div>
  </div>
</section>

<footer class="footer">
  <div class="wrap">
    <div class="logo-col"><div class="brand" style="font-size:20px"><span class="dot"></span>The Kelvale Clinic</div></div>
    <div class="col" style="width:245px">
      <h6>CONTACT US</h6>
      <ul class="contact">
        <li><i></i>1300 555 014 (Phone)</li>
        <li><i></i>1300 555 015 (Fax)</li>
        <li><i></i>info@thekelvaleclinic.com.au</li>
        <li><i></i>424 Lorem Ipsum Dummy<br>Lorem Ipsum</li>
      </ul>
    </div>
    <div class="col" style="width:265px">
      <h6>NEWSLETTER</h6>
      <p>Register Your email address to get information about us</p>
      <div class="email">Email Address</div>
      <span class="subscribe">SUBSCRIBE</span>
    </div>
    <div class="col" style="flex:1">
      <h6>FOLLOW US</h6>
      <p>Lorem ipsum dolor sit amet, conse ctetur adipiscing elit. Nulla in purus nibh. Donec ornare</p>
      <div class="fsocial"><span></span><span></span><span></span><span></span><span></span></div>
    </div>
  </div>
</footer>
<div class="copyright">© Copyright 2017 The Kelvale Clinic All Rights Reserved</div>

</body>
</html>
```